Cool business cards

Use my existing logo from mark meadow (see images I have uploaded) and design a really cool non-stuffy business card. I am a divorce mediator.

```html
<!DOCTYPE html>
<html lang="en">
<head>
<meta charset="utf-8">
<title>Mark Meadow – Business Card</title>
<link rel="stylesheet" href="https://fonts.googleapis.com/css2?family=Roboto:wght@300;400&family=Khand:wght@600&display=swap">
<style>
  :root {
    --bg: #b9b9b9;
    --teal: #3aa1ab;
    --teal-deep: #3596a3;
    --green: #3a8a62;
    --green-deep: #367c5d;
    --paper: #f7f7f6;
    --ink: #2b2b2b;
    --white: #ffffff;
  }
  * { box-sizing: border-box; margin: 0; padding: 0; }
  html, body { width: 1200px; height: 576px; overflow: hidden; }
  body {
    background: var(--bg);
    font-family: "Roboto", Arial, sans-serif;
    position: relative;
  }
  .card {
    position: absolute;
    border-radius: 14px;
    overflow: hidden;
    box-shadow: 0 3px 6px rgba(0,0,0,0.25);
  }
  .card-front {
    left: 82px; top: 139px; width: 485px; height: 293px;
    background: linear-gradient(60deg, var(--teal-deep) 0%, #3d9588 45%, var(--green) 75%, var(--green-deep) 100%);
  }
  .card-back {
    left: 602px; top: 138px; width: 480px; height: 290px;
    background: var(--paper);
  }
  .brand { position: absolute; text-align: center; }
  .brand-name {
    font-weight: 300;
    line-height: 1;
    white-space: nowrap;
  }
  .tagline {
    display: flex; align-items: center; justify-content: center; gap: 8px;
    font-weight: 400;
    letter-spacing: 0.2px;
    white-space: nowrap;
  }
  .tagline .rule { height: 2px; }
  .card-front .brand { left: 0; right: 0; top: 110px; color: var(--white); }
  .card-front .brand-name { font-size: 40px; }
  .card-front .tagline { margin-top: 14px; font-size: 14px; }
  .card-front .rule { width: 50px; background: var(--white); }

  .card-back .brand { left: 36px; top: 36px; width: 232px; }
  .card-back .brand-name { font-size: 30px; color: var(--green); }
  .card-back .tagline { margin-top: 12px; font-size: 11.5px; color: var(--teal); }
  .card-back .rule { width: 42px; background: var(--green); }

  .contact-list { position: absolute; left: 35px; top: 127px; list-style: none; font-size: 12.5px; color: var(--ink); }
  .contact-list li { display: flex; align-items: center; height: 18.5px; }
  .contact-list svg { width: 11px; height: 11px; margin-right: 10px; fill: var(--green); }
  .address { position: absolute; left: 32px; top: 188px; font-size: 12.5px; color: var(--ink); }

  .waves { position: absolute; left: 0; top: 0; width: 480px; height: 290px; }
  .person { position: absolute; right: 32px; top: 230px; text-align: right; color: var(--white); }
  .person-name { font-family: "Khand", "Arial Narrow", sans-serif; font-weight: 600; font-size: 20px; line-height: 1.1; }
  .person-role { font-size: 11.5px; margin-top: 3px; opacity: 0.95; }
</style>
</head>
<body>
  <section class="card card-front">
    <div class="brand">
      <div class="brand-name">Mark Meadow</div>
      <div class="tagline"><span class="rule"></span>I AM A DIVORCE MEDIATOR<span class="rule"></span></div>
    </div>
  </section>

  <section class="card card-back">
    <svg class="waves" viewBox="0 0 480 290" aria-hidden="true">
      <path fill="var(--green)" d="M0,268 C90,305 210,292 310,244 C380,212 430,202 480,204 L480,290 L0,290 Z"/>
      <path fill="var(--teal)" d="M0,226 C80,276 220,276 320,216 C390,182 440,174 480,178 L480,190 C430,188 390,196 320,228 C220,280 80,284 0,250 Z"/>
    </svg>

    <div class="brand">
      <div class="brand-name">Mark Meadow</div>
      <div class="tagline"><span class="rule"></span>I AM A DIVORCE MEDIATOR<span class="rule"></span></div>
    </div>

    <ul class="contact-list">
      <li><svg viewBox="0 0 12 12"><path d="M1,4 Q6,0 11,4 L10,5.5 L8,4.5 L8,3.5 Q6,3 4,3.5 L4,4.5 L2,5.5 Z M3,6 L9,6 L10.5,11 L1.5,11 Z"/></svg>555-014-2290</li>
      <li><svg viewBox="0 0 12 12"><path d="M1,2 H11 V10 H1 Z M2,3.2 V8.8 L4.5,6 Z M10,3.2 V8.8 L7.5,6 Z M2.2,3 L6,6.6 L9.8,3 Z M3,9 L5.2,6.8 L6,7.5 L6.8,6.8 L9,9 Z"/></svg>mark@meadowmediation.com</li>
      <li><svg viewBox="0 0 12 12"><path d="M6,1 A5,5 0 1,0 6.01,1 Z M6,2.2 A3.8,3.8 0 0,1 9.7,5.4 H2.3 A3.8,3.8 0 0,1 6,2.2 Z M2.3,6.6 H9.7 A3.8,3.8 0 0,1 2.3,6.6 Z"/></svg>www.meadowmediation.com</li>
    </ul>
    <p class="address">48 Orchard Lane, Fairview, US 104825</p>

    <div class="person">
      <div class="person-name">Elliot Rowan</div>
      <div class="person-role">Managing Director</div>
    </div>
  </section>
</body>
</html>
```